Hop Bright Meadow Business Website Branding

Looking for a wordpress template design with CSS and HTML encoding. Current website can be seen at hopbrightmeadow.example.

WE ARE CURRENTLY IN PROCESS GETTING A LOGO DESIGN... I HAVE INCLUDED THE TOP POTENTIAL DESIGNS FOR REFERENCE TO HELP UNDERSTAND WHAT STYLE WE ARE LOOKING FOR...
NOTE: THE “PEBBLE CREW” LOGO WAS A PREVIOUS COMPANY WE OWNED SO YOU CAN GE A FEEL FOR THE TYPE OF DESIGNS WE HAVE USED IN THE PAST.

My blog will focus on making a connection with wild Florida, it’s wildlife, plants and animals... with an eye toward Florida conservation, nature adventure trips, and education... Content, photos and other merchandise will also be offered for sale.
I’m looking for a site design that incorporates Florida nature and wildlife/plants, with a fun “Old Florida” retro-adventure feel.
When they see this site it should speak to the import of natural Florida and the critical nature of the ecosystem here... while being instantly recognizable and iconic... IE: when I think of florida I think of water, plants, warmth, sunsets etc...

https://join.chatroomhub.example/t/lumexstudio-kzt4821/shared_invite/zt-pqwrt83m-hRnLvXaKoPzsYcB1Uq7JdM

Target Market(s)

Nature, Education, Conservation, Photography

Industry/Entity Type

Photographer

Coding

Coded - Design and coding required

Requirements
Must have
• Need to have site wide template design which generally includes a landing page and a general page template for other pages... Must include html and css encoding...
Should not have
• Any animals included in the site should be Florida native... IE: no African animals etc... This will require some research to ensure that if animals are included that they are part of the Florida ecosystem.

```html
<!DOCTYPE html>
<html lang="en">
<head>
<meta charset="utf-8">
<title>Hop Bright Meadow</title>
<link href="https://fonts.googleapis.com/css2?family=Roboto+Slab:wght@300;400;700;800&family=IBM+Plex+Sans:wght@400;500;600&display=swap" rel="stylesheet">
<style>
:root{
  --sand:#f7d7b5;
  --sand-deep:#efc9a2;
  --forest:#2f4210;
  --forest-dark:#1f2e08;
  --moss:#4a6a1c;
  --ember:#e0793a;
  --bark:#3a1f12;
  --ink:#2b2b2b;
  --muted:#8a6f5a;
  --white:#ffffff;
}
*{box-sizing:border-box;margin:0;padding:0}
html,body{width:1200px;height:4064px;overflow:hidden}
body{background:var(--sand);font-family:"IBM Plex Sans",sans-serif;color:var(--ink);position:relative}
.abs{position:absolute}
/* header */
.site-header{position:absolute;left:0;top:0;width:1200px;height:103px;background:var(--sand);z-index:5}
.nav{position:absolute;top:56px;display:flex;gap:40px;font-family:"Roboto Slab",serif;font-size:15px;color:var(--bark);letter-spacing:.3px}
.nav-left{left:109px}
.nav-right{left:752px}
.nav a{color:inherit;text-decoration:none;position:relative}
.nav a.active::after{content:"";position:absolute;left:6px;right:6px;bottom:-9px;height:2px;background:var(--bark)}
.brand{position:absolute;left:470px;top:-50px;width:260px;height:260px;border-radius:50%;background:var(--sand);z-index:6;display:flex;align-items:center;justify-content:center;padding-top:90px}
.brand-name{font-family:"Roboto Slab",serif;font-weight:700;font-size:22px;color:var(--forest);text-align:center;line-height:1.1;width:150px}
.brand-dot{position:absolute;left:112px;top:62px;width:36px;height:36px;border-radius:50%;background:var(--forest)}
/* hero */
.hero{position:absolute;left:0;top:103px;width:1200px;height:760px;background:linear-gradient(180deg,#7d7f7a 0%,#5e6a55 22%,#3f5a22 45%,#2f4a17 70%,#3c5a1d 100%)}
.hero-title{position:absolute;left:0;width:1200px;top:277px;text-align:center;font-family:"Roboto Slab",serif;font-weight:700;font-size:42px;line-height:60px;color:var(--white);text-shadow:0 2px 6px rgba(0,0,0,.45);letter-spacing:.5px}
.btn{display:inline-flex;align-items:center;justify-content:center;background:var(--forest-dark);color:var(--white);font-family:"IBM Plex Sans",sans-serif;font-weight:500;font-size:14px;letter-spacing:.5px;border-radius:26px;height:52px;width:156px;text-decoration:none}
.hero .btn{position:absolute;left:522px;top:410px;height:50px}
.hero-wave{position:absolute;left:0;top:690px}
/* headings */
.h2{font-family:"Roboto Slab",serif;font-size:34px;color:var(--bark);letter-spacing:.3px;white-space:nowrap}
.h2 .light{font-weight:300}
.h2 .bold{font-weight:700}
.rule{width:104px;height:3px;background:var(--ember)}
.body-copy{font-size:13.5px;line-height:34px;color:var(--muted)}
/* circles */
.photo-ring{position:absolute;border-radius:50%}
.photo-circle{position:absolute;border-radius:50%;border:4px solid var(--sand)}
/* wonders */
.wonders-title{position:absolute;left:0;width:1200px;top:1582px;text-align:center;font-family:"Roboto Slab",serif;font-size:34px;color:var(--white)}
.wonders-title .light{font-weight:300}.wonders-title .bold{font-weight:700}
.grid{position:absolute;left:109px;top:1687px;display:grid;grid-template-columns:repeat(3,317px);grid-auto-rows:256px;column-gap:15px;row-gap:19px}
.tile{border:3px solid var(--white)}
/* blogs */
.blogs-title{position:absolute;left:0;width:1200px;top:2960px;text-align:center;font-family:"Roboto Slab",serif;font-weight:700;font-size:40px;color:var(--bark)}
.blog-list{position:absolute;left:110px;top:3075px;display:flex;gap:13px}
.blog-card{width:317px}
.blog-img{height:256px;border-radius:4px;box-shadow:0 2px 6px rgba(0,0,0,.2)}
.blog-date{margin-top:22px;font-size:14px;color:var(--bark)}
.blog-title{margin-top:14px;font-family:"IBM Plex Sans",sans-serif;font-weight:600;font-size:13.5px;line-height:28px;color:var(--bark);text-transform:uppercase}
/* footer */
.footer{position:absolute;left:0;top:3500px;width:1200px;height:564px}
.footer-nav{position:absolute;left:0;width:1200px;top:238px;display:flex;justify-content:center;gap:38px;font-family:"Roboto Slab",serif;font-size:15px;color:var(--white)}
.footer-rule{position:absolute;left:110px;width:980px;height:1px;background:rgba(255,255,255,.55)}
.contact{position:absolute;top:317px;width:300px;text-align:center;color:var(--white)}
.contact-icon{width:56px;height:56px;border-radius:50%;border:1.5px solid var(--white);margin:0 auto;display:flex;align-items:center;justify-content:center}
.contact-text{margin-top:22px;font-size:14px;line-height:34px}
.contact-text.big{font-size:19px;margin-top:18px}
.copyright{position:absolute;left:0;width:1200px;top:510px;text-align:center;color:var(--white);font-size:14px}
</style>
</head>
<body>

<header class="site-header">
  <nav class="nav nav-left">
    <a class="active">HOME</a><a>ABOUT</a><a>GALLER</a><a>BLOGS</a>
  </nav>
  <nav class="nav nav-right">
    <a>TESTIMONIALS</a><a>CONTACT</a><a>&#9679; LOGIN</a>
  </nav>
</header>

<section class="hero" role="img" aria-label="Photo of lush green canyon with tall waterfalls under a cloudy sky">
  <div class="hero-title">EXPLORING FLORIDA’S NATURAL<br>WONDERS</div>
  <a class="btn">GET STARTED</a>
  <svg class="hero-wave" width="1200" height="80" viewBox="0 0 1200 80">
    <path d="M0 80 L0 20 C60 40 120 30 200 10 C260 -4 320 10 380 30 C450 50 520 46 600 22 C680 0 760 8 840 30 C920 52 1000 52 1080 30 C1130 16 1170 12 1200 20 L1200 80 Z" fill="var(--sand)"/>
  </svg>
</section>

<div class="brand">
  <span class="brand-dot"></span>
  <span class="brand-name">Hop Bright Meadow</span>
</div>

<!-- about the site -->
<div class="photo-ring" style="left:114px;top:942px;width:448px;height:448px;background:linear-gradient(135deg,var(--ember) 0%,var(--ember) 40%,var(--forest) 60%,var(--forest) 100%)"></div>
<div class="photo-circle" role="img" aria-label="Photo of a misty pine forest at sunrise" style="left:122px;top:944px;width:440px;height:440px;background:radial-gradient(circle at 60% 60%,#d9a23e 0%,#8a6a2a 25%,#3d3a1f 55%,#20240f 100%)"></div>
<div class="abs h2" style="left:599px;top:1000px"><span class="light">ABOUT </span><span class="bold">HOP BRIGHT MEADOW</span></div>
<div class="abs rule" style="left:599px;top:1057px"></div>
<p class="abs body-copy" style="left:599px;top:1080px;width:490px">Come explore wild places and stunning scenery with me as I discover new and exciting eco-adventures and learn about the rare and unique wildlife and environments that make Florida so precious and extraordinary. I hope you can vicariously enjoy the wild and untamed beauty of Florida through my eyes, and learn some amazing things about nature on our explorations.</p>
<a class="abs btn" style="left:599px;top:1276px">READ MORE</a>

<!-- wonders band -->
<svg class="abs" style="left:0;top:1490px" width="1200" height="855" viewBox="0 0 1200 855">
  <defs>
    <linearGradient id="leaf" x1="0" y1="0" x2="1" y2="1">
      <stop offset="0" stop-color="#3b5714"/><stop offset=".5" stop-color="#2f4710"/><stop offset="1" stop-color="#3e5c18"/>
    </linearGradient>
  </defs>
  <polygon points="0,0 1200,46 1200,72 0,20" fill="var(--ember)" opacity=".85"/>
  <polygon points="0,8 1200,62 1200,850 0,760" fill="url(#leaf)"/>
  <polygon points="0,740 1200,812 1200,790 0,760" fill="var(--ember)" opacity=".85"/>
</svg>
<div class="wonders-title"><span class="light">FLORIDA’S </span><span class="bold">NATURAL WONDERS</span></div>
<div class="abs rule" style="left:548px;top:1640px"></div>
<div class="grid">
  <div class="tile" role="img" aria-label="Photo of a kayak on a sunlit forest river" style="background:linear-gradient(180deg,#5d7a3a,#2e4a2a 60%,#7fa0b0)"></div>
  <div class="tile" role="img" aria-label="Photo of two white ibises wading at golden hour" style="background:linear-gradient(180deg,#3a2a12,#b47a2a 55%,#d8a24a)"></div>
  <div class="tile" role="img" aria-label="Photo of an alligator resting on a log by water" style="background:linear-gradient(180deg,#2e5a22,#3b4a30 55%,#22302a)"></div>
  <div class="tile" role="img" aria-label="Photo of a Florida panther among green foliage" style="background:linear-gradient(135deg,#5a7a4a,#8a7a5a 50%,#4a6a3a)"></div>
  <div class="tile" role="img" aria-label="Photo of a young striped animal wading in a stream" style="background:linear-gradient(180deg,#2f5a1f,#3a3a2a 60%,#5a6a5a)"></div>
  <div class="tile" role="img" aria-label="Photo of a pier at sunset over calm water" style="background:linear-gradient(180deg,#3a6aa8,#e0913a 45%,#2a4a7a 60%,#1a3a6a)"></div>
</div>

<!-- about me -->
<div class="abs h2" style="left:109px;top:2498px;font-weight:700;font-size:40px">ABOUT ME</div>
<div class="abs rule" style="left:109px;top:2566px"></div>
<p class="abs body-copy" style="left:109px;top:2594px;width:470px">Hello nature lovers! I’m Marla Quenby, a wildlife educator, Florida Master Naturalist, nature writer and photographer, busy mama of three kiddos, a playful Havanese puppy, two very chubby guinea pigs, and a giant tree frog. I have a passion for all things nature and I adore living in Southwest Florida&nbsp; I will always be a California girl,</p>
<a class="abs btn" style="left:109px;top:2781px">READ MORE</a>
<div class="photo-ring" style="left:641px;top:2434px;width:448px;height:448px;background:linear-gradient(135deg,var(--forest) 0%,var(--forest) 45%,var(--ember) 60%,var(--ember) 100%)"></div>
<div class="photo-circle" role="img" aria-label="Portrait photo of the site author by the sea at sunset" style="left:649px;top:2440px;width:440px;height:440px;background:linear-gradient(160deg,#d8924a 0%,#8a6a5a 40%,#3aa0b0 80%,#2a8aa0 100%)"></div>

<!-- latest blogs -->
<div class="blogs-title">LATEST BLOGS</div>
<div class="abs rule" style="left:548px;top:3034px"></div>
<div class="blog-list">
  <article class="blog-card">
    <div class="blog-img" role="img" aria-label="Photo of a red and yellow lily flower" style="background:linear-gradient(135deg,#e0502a,#f07a2a 45%,#c8b02a 70%,#4a6a2a)"></div>
    <div class="blog-date">September 24th-October 22nd, 2020</div>
    <div class="blog-title">Communing with nature at Fernwick Hollow Preserve Trails</div>
  </article>
  <article class="blog-card">
    <div class="blog-img" role="img" aria-label="Photo of small white wildflowers in a pine clearing" style="background:linear-gradient(180deg,#6a8a5a,#3a5a22 50%,#2a4a1a)"></div>
    <div class="blog-date">September 24th-October 22nd, 2020</div>
    <div class="blog-title">Lorem ipsum dolor sit amet, consectetur adipiscing elit</div>
  </article>
  <article class="blog-card">
    <div class="blog-img" role="img" aria-label="Photo of a small dark fossil held between fingers" style="background:linear-gradient(135deg,#5a7a3a,#4a6a2a 45%,#e0a090 75%,#c88070)"></div>
    <div class="blog-date">September 24th-October 22nd, 2020</div>
    <div class="blog-title">Lorem ipsum dolor sit amet, consectetur adipiscing elit</div>
  </article>
</div>

<!-- footer -->
<footer class="footer">
  <svg class="abs" style="left:0;top:0" width="1200" height="564" viewBox="0 0 1200 564">
    <defs>
      <linearGradient id="foot" x1="0" y1="0" x2="0" y2="1">
        <stop offset="0" stop-color="#2f4510"/><stop offset="1" stop-color="#3a5418"/>
      </linearGradient>
    </defs>
    <path d="M0 40 C80 70 160 60 240 30 C320 0 400 10 480 40 C560 70 640 72 720 44 C800 16 880 6 960 30 C1040 54 1120 56 1200 40 L1200 564 L0 564 Z" fill="url(#foot)"/>
  </svg>
  <nav class="footer-nav"><span>HOME</span><span>ABOUT</span><span>GALLERY</span><span>BLOGS</span><span>TESTIMONIALS</span><span>CONTACT</span></nav>
  <div class="footer-rule" style="top:292px"></div>
  <div class="contact" style="left:144px">
    <div class="contact-icon"><svg width="20" height="20" viewBox="0 0 24 24"><path d="M6.6 10.8a15 15 0 0 0 6.6 6.6l2.2-2.2a1 1 0 0 1 1-.25 11.4 11.4 0 0 0 3.6.57 1 1 0 0 1 1 1V20a1 1 0 0 1-1 1A17 17 0 0 1 3 4a1 1 0 0 1 1-1h3.5a1 1 0 0 1 1 1c0 1.25.2 2.45.57 3.57a1 1 0 0 1-.25 1z" fill="#fff"/></svg></div>
    <div class="contact-text big">123-456-7890</div>
  </div>
  <div class="contact" style="left:435px">
    <div class="contact-icon"><svg width="18" height="22" viewBox="0 0 24 30"><path d="M12 1a10 10 0 0 0-10 10c0 7.5 10 18 10 18s10-10.5 10-18A10 10 0 0 0 12 1zm0 13.5A3.5 3.5 0 1 1 12 7.5a3.5 3.5 0 0 1 0 7z" fill="#fff"/></svg></div>
    <div class="contact-text">Lorem ipsum dolor sit amet, consectetur<br>adipiscing elit,Florida</div>
  </div>
  <div class="contact" style="left:736px">
    <div class="contact-icon"><svg width="22" height="16" viewBox="0 0 24 18"><path d="M1 1h22v16H1z" fill="#fff"/><path d="M1 1l11 9 11-9" fill="none" stroke="#2f4510" stroke-width="2"/></svg></div>
    <div class="contact-text">infohopbrightmeadow.example</div>
  </div>
  <div class="footer-rule" style="top:482px"></div>
  <div class="copyright">©2020 All Rights Reserved</div>
</footer>

</body>
</html>
```